Climbing Gear Company Stationary Design

We need some new stationary to standardise our business.
We require:

Business Card
A4 Letterhead
With complements slip

Our business is a Distributor and retailer of rock climbing equipment throughout Australia.
We need to the stationary (business card in particular) to reflect this.

Target Market(s)

customers, other retail outlets, overseas manufacturers.

Industry/Entity Type

Business

Requirements
Must have
• company logo
website url- www.ridgetopgearworks.com.au
email - mark@ridgetopgearworks.com
Business Address: Unit 3, 14-16 Marlowe Street, Coffs Harbour, NSW, 2371
Phone: 0438 627 194
my Name (on Business card) - Gordon Pellimore
use of Blue colour in our logo

```html
<!DOCTYPE html>
<html lang="en">
<head>
<meta charset="utf-8">
<title>Ridgetop Gearworks – Business Card</title>
<link href="https://fonts.googleapis.com/css2?family=Open+Sans:wght@400;600;700;800&display=swap" rel="stylesheet">
<style>
  :root {
    --brand-blue: #21428b;
    --paper: #ffffff;
    --band-light: #f4f4f5;
    --band-mid: #dcdcde;
    --rule-grey: #c4c4c8;
    --backdrop: #eceae6;
  }
  * { margin: 0; padding: 0; box-sizing: border-box; }
  html, body {
    width: 1200px; height: 483px; overflow: hidden;
    background: var(--backdrop);
    font-family: "Open Sans", Arial, sans-serif;
  }
  .stage { position: relative; width: 1200px; height: 483px; }
  .card {
    position: absolute; top: 104px; width: 527px; height: 300px;
    border-radius: 14px; overflow: hidden;
    box-shadow: 0 3px 8px rgba(0,0,0,0.25);
  }
  .card--front { left: 50px; background: var(--brand-blue); color: var(--paper); }
  .card--back { left: 618px; background: var(--paper); color: var(--brand-blue); }

  .holder-name {
    position: absolute; top: 40px; left: 0; width: 100%;
    text-align: center; font-weight: 700; font-size: 14px; letter-spacing: 0.2px;
  }
  .brand-band {
    position: absolute; left: 0; width: 100%;
    background: linear-gradient(90deg, var(--band-light) 0%, #e7e7e9 60%, var(--band-mid) 100%);
  }
  .card--front .brand-band { top: 109px; height: 71px; }
  .card--back .brand-band { top: 107px; height: 79px; }
  .band-rule { position: absolute; left: 0; width: 100%; height: 2px; }
  .card--front .band-rule { background: rgba(255,255,255,0.85); }
  .card--back .band-rule { background: var(--rule-grey); }
  .band-wedge { position: absolute; left: 0; top: 0; height: 100%; }
  .brand-lockup {
    position: absolute; left: 0; width: 100%; text-align: center; color: var(--brand-blue);
  }
  .brand-name {
    display: block; font-weight: 800; font-size: 28px; letter-spacing: 0.8px; line-height: 1;
  }
  .brand-tagline {
    display: block; margin-top: 7px; font-weight: 400; font-size: 12px; letter-spacing: 2.6px;
  }
  .contact {
    position: absolute; left: 0; width: 100%; text-align: center; font-size: 11.5px;
  }
  .contact--address { top: 229px; }
  .contact--lines { top: 249px; word-spacing: 1px; }
  .contact--lines span + span { margin-left: 12px; }
  .web-url {
    position: absolute; top: 226px; left: 0; width: 100%; text-align: center;
    font-size: 12px; letter-spacing: 2.4px;
  }
</style>
</head>
<body>
<main class="stage">
  <section class="card card--front">
    <p class="holder-name">GORDON PELLIMORE</p>
    <div class="band-rule" style="top:104px"></div>
    <div class="brand-band">
      <svg class="band-wedge" width="60" height="71" viewBox="0 0 60 71" aria-hidden="true">
        <polygon points="0,0 18,0 60,71 0,71" fill="#ffffff"/>
      </svg>
      <div class="brand-lockup" style="top:13px">
        <span class="brand-name">RIDGETOP GEARWORKS</span>
        <span class="brand-tagline">THE ROPES•THE ROCK•THE ADVENTURE</span>
      </div>
    </div>
    <div class="band-rule" style="top:183px"></div>
    <p class="contact contact--address">Unit 3, 14-16 Marlowe Street Coffs Harbour, NSW, 2371</p>
    <p class="contact contact--lines">
      <span>P : 0438 627 194</span><span>E : mark@ridgetopgearworks.com</span><span>W: www.ridgetopgearworks.com.</span>
    </p>
  </section>

  <section class="card card--back">
    <div class="band-rule" style="top:104px"></div>
    <div class="brand-band">
      <svg class="band-wedge" width="64" height="79" viewBox="0 0 64 79" aria-hidden="true">
        <polygon points="0,0 18,0 64,79 0,79" fill="#ffffff"/>
      </svg>
      <div class="brand-lockup" style="top:17px">
        <span class="brand-name">RIDGETOP GEARWORKS</span>
        <span class="brand-tagline">THE ROPES•THE ROCK•THE ADVENTURE</span>
      </div>
    </div>
    <div class="band-rule" style="top:185px"></div>
    <p class="web-url">www.ridgetopgearworks.com.</p>
  </section>
</main>
</body>
</html>
```